Professional violinist needs business cards

I am trying to attract the following jobs:
-private violin lessons (primarily classical)
-performance gigs (weddings, birthday parties, funerals, etc.)
-collaborations with other artists (studio recordings, performances)

I want to communicate that I have a very high standard of excellence for my work, but I also love people and celebrations.
Values/style words I like are:
love, joy, peace, fun, beauty, authenticity, excellence, warmth, refined/sleek, free spirited. If that's too confusing, just ignore :)

I will attach my favorite business card template that I could find on Canva. The lines are supposed to be like a music staff, which I think is really cool, but I also don't want it to look too busy. I like the simple black and white--I think it looks sharp--but I also am open to other ideas. I also have seen business cards with pictures included that looked great, so I attached an image that could be used as well.

I am also attaching a file that I made of my initials that could be used as a logo, but I'm not sure if it should be included.

Information on the card:
-My name (18 letters total)
-"violinist"
-phone number, email, website

Thank you!

```html
<!DOCTYPE html>
<html lang="en">
<head>
<meta charset="utf-8">
<title>Marina Kessler — Violinist Business Card</title>
<link href="https://fonts.googleapis.com/css2?family=Barlow+Condensed:wght@300;400;600&family=Barlow:wght@500&display=swap" rel="stylesheet">
<style>
  :root {
    --paper: #ffffff;
    --ink: #111111;
    --card-black: #000000;
    --backdrop: #e9e7e3;
    --photo-dark: #1c1c1c;
    --photo-mid: #6d6d6d;
    --photo-light: #d9d9d9;
  }
  * { box-sizing: border-box; margin: 0; padding: 0; }
  html, body {
    width: 1200px; height: 1200px; overflow: hidden;
    background: var(--backdrop);
  }
  .sheet {
    width: 1200px; height: 1200px;
    display: flex; flex-direction: column; align-items: center; justify-content: center;
    gap: 56px;
  }
  .card {
    width: 900px; height: 514px;
    position: relative; overflow: hidden;
    box-shadow: 0 6px 18px rgba(0,0,0,0.18);
  }

  /* Back side */
  .card-back {
    background: var(--card-black);
    display: flex; align-items: center; justify-content: center;
  }
  .back-mark {
    display: flex; align-items: center; gap: 22px;
    color: var(--paper);
    font-family: "Barlow Condensed", sans-serif;
    font-weight: 400; font-size: 64px; letter-spacing: 0.02em;
  }
  .back-mark .dot {
    width: 22px; height: 22px; border-radius: 50%; background: var(--paper);
  }

  /* Front side */
  .card-front { background: var(--paper); }
  .portrait {
    position: absolute; top: 0; right: 0; width: 470px; height: 100%;
    background:
      radial-gradient(ellipse at 72% 30%, var(--photo-light) 0%, var(--photo-mid) 28%, transparent 55%),
      linear-gradient(90deg, rgba(255,255,255,1) 0%, rgba(160,160,160,0.85) 20%, var(--photo-mid) 42%, var(--photo-dark) 75%, var(--photo-dark) 100%);
  }
  .identity {
    position: absolute; left: 96px; top: 150px;
    font-family: "Barlow Condensed", sans-serif; color: var(--ink);
  }
  .name { font-size: 48px; line-height: 1; letter-spacing: 0.01em; }
  .name .first { font-weight: 600; }
  .name .last { font-weight: 300; }
  .role {
    margin-top: 10px; font-size: 21px; font-weight: 400; letter-spacing: 0.34em;
  }
  .contacts {
    position: absolute; left: 96px; top: 300px;
    list-style: none;
    font-family: "Barlow", sans-serif; font-weight: 500; font-size: 28px; color: var(--ink);
  }
  .contacts li { display: flex; align-items: center; gap: 20px; height: 52px; }
  .contacts svg { width: 28px; height: 28px; flex: none; }
</style>
</head>
<body>
<main class="sheet">
  <section class="card card-back" aria-label="Card back">
    <div class="back-mark"><span class="dot"></span><span>Marina Kessler</span></div>
  </section>

  <section class="card card-front" aria-label="Card front">
    <div class="portrait" role="img" aria-label="Black and white photo of the violinist holding her violin and bow beside a stone wall, blending into the card with a brushed edge"></div>
    <div class="identity">
      <h1 class="name"><span class="first">MARINA</span> <span class="last">KESSLER</span></h1>
      <p class="role">VIOLINIST</p>
    </div>
    <ul class="contacts">
      <li>
        <svg viewBox="0 0 24 24" aria-hidden="true"><path fill="#111" d="M6.6 2.5c.6-.3 1.3-.1 1.6.5l1.9 3.6c.3.6.1 1.2-.4 1.6L8.3 9.3c.9 2.4 2.6 4.6 4.6 6.2l1.3-1.2c.5-.4 1.2-.5 1.7-.1l3.3 2.4c.5.4.6 1.1.3 1.7l-1.2 2c-.5.8-1.5 1.2-2.4.9C9.4 19.4 4.6 13.6 3.5 7.1c-.2-.9.3-1.8 1.1-2.3z"/></svg>
        <span>(555) 218 - 4630</span>
      </li>
      <li>
        <svg viewBox="0 0 24 24" aria-hidden="true"><rect x="2" y="5" width="20" height="14" fill="#111"/><path d="M2.5 5.5 12 13l9.5-7.5M2.5 18.5 9.5 11.5M21.5 18.5 14.5 11.5" stroke="#fff" stroke-width="1.4" fill="none"/></svg>
        <span>marinakessler@mailbox.com</span>
      </li>
      <li>
        <svg viewBox="0 0 24 24" aria-hidden="true"><circle cx="12" cy="12" r="10" fill="#111"/><g stroke="#fff" stroke-width="1.1" fill="none"><ellipse cx="12" cy="12" rx="4.5" ry="10"/><path d="M2 12h20M3.5 7h17M3.5 17h17M12 2v20"/></g></svg>
        <span>www.marinakessler.com</span>
      </li>
    </ul>
  </section>
</main>
</body>
</html>
```